A5 Flyer for Financial Services Business

I am after a re-design of our business flyer to fit in with our new branding style and logo colour scheme. Wanting something with a bit of designer flair that I could not create myself. I have included the flyer which I created which lacks style so dazzle me.

I want to use the same content.

Text for main body of flyer is

Are you a small business owner, tradie or TRPQ Service Provider struggling to stay on top of your bookkeeping and compliance obligations? If so we would love to help you get back on track and take control of your business finances so that you can make informed business decisions and focus on what you do best.

We have over 20 years industry experience and, as a small business ourselves, we are able to offer our clients a personal bookkeeping solution tailored to meet the needs of your business.

Accounts Payable | Accounts Receivable
Customer Invoicing
Bank and Credit Card Reconciliations
Payroll | Superannuation | Payroll Tax
Business Activity | Instalment Activity Statements
Regular Financial Reports
Vantly and Brimfolk Set-Up and Training

```html
<!DOCTYPE html>
<html lang="en">
<head>
<meta charset="utf-8">
<title>Even Ledger Financial Services – Bookkeeping Flyer</title>
<link href="https://fonts.googleapis.com/css2?family=Montserrat:wght@400;500;600;700;800&family=Oswald:wght@500;600&display=swap" rel="stylesheet">
<style>
:root{
  --teal:#0f8f8a;
  --teal-deep:#0b5e6b;
  --teal-light:#3fb3a8;
  --gray:#7b7c80;
  --gray-dark:#5f6064;
  --gray-soft:#e4e6e9;
  --navy:#0e2b4b;
  --ink:#2a2d33;
  --paper:#ffffff;
  --stage:#eceef1;
}
*{margin:0;padding:0;box-sizing:border-box}
html,body{width:1200px;height:2731px;overflow:hidden;background:var(--stage)}
body{font-family:"Montserrat",sans-serif;color:var(--ink)}
.flyer{position:absolute;left:50px;top:585px;width:1100px;height:1561px;background:var(--paper);overflow:hidden;box-shadow:0 20px 50px rgba(0,0,0,.25)}
.abs{position:absolute}
.brand{left:72px;top:72px;display:flex;align-items:center;gap:18px}
.brand-mark{width:74px;height:74px;background:var(--teal-deep)}
.brand-name{font-size:46px;font-weight:400;color:var(--teal-deep);line-height:1;letter-spacing:.5px}
.brand-sub{font-size:21px;font-weight:400;letter-spacing:11px;color:var(--gray);margin-top:4px}
.hero-band{left:0;top:196px;width:1100px;height:282px;background:linear-gradient(90deg,var(--teal-deep),var(--teal))}
.hero-photo{left:0;top:0}
.headline{left:72px;top:246px;font-size:58px;font-weight:800;color:#fff;line-height:1}
.tagline{left:72px;top:376px;width:460px;height:58px;background:var(--gray);color:#fff;font-size:30px;font-weight:800;display:flex;align-items:center;justify-content:center;border:3px solid rgba(255,255,255,.35)}
.intro-icon{left:80px;top:522px}
.intro{left:213px;top:524px;font-size:25px;line-height:1.4;color:var(--ink)}
.intro .accent{color:var(--teal);font-weight:600}
.intro-head{font-family:"Oswald",sans-serif;font-weight:600;font-size:44px;color:var(--navy);line-height:1.1;letter-spacing:-.5px}
.intro-box{left:75px;top:655px;width:950px;height:113px;border:3px solid var(--teal-deep);padding:10px 24px;font-size:24px;line-height:1.2;color:var(--ink)}
.side-photo{left:75px;top:812px;width:316px;height:450px;border:4px solid var(--teal-deep);border-radius:22px;overflow:hidden}
.seal{left:148px;top:1217px}
.bas{left:75px;top:1390px;width:320px;text-align:center;font-size:23px;color:var(--ink)}
.years{left:422px;top:812px;color:var(--ink)}
.years .small{font-size:26px}
.years .big{font-family:"Oswald",sans-serif;font-weight:500;font-size:46px;color:var(--navy);line-height:1}
.years-divider{left:638px;top:826px;width:2px;height:60px;background:var(--gray)}
.years-note{left:671px;top:828px;font-size:24px;line-height:1.25}
.offer{left:391px;top:891px}
.offer-text{left:422px;top:905px;color:#fff}
.offer-text .small{font-size:25px}
.offer-text .big{font-family:"Oswald",sans-serif;font-weight:500;font-size:49px;line-height:1}
.offer-text .big.teal{color:var(--teal-deep)}
.services{display:flex;flex-direction:column;list-style:none;font-size:23px;font-weight:600;color:var(--ink)}
.services li{position:relative;padding-left:30px;line-height:1.25}
.services li svg{position:absolute;left:0;top:6px}
.col-a{left:422px;top:1118px}
.col-b{left:745px;top:1118px}
.col-divider{left:717px;top:1120px;width:2px;height:285px;background:var(--gray)}
.footer{left:0;top:1435px}
.partner{width:78px;height:78px;border-radius:50%}
.partners{left:80px;top:1471px;display:flex;gap:6px;align-items:center}
.call{left:565px;top:1452px;color:#fff;font-size:40px;font-weight:400;display:flex;align-items:center;gap:10px;white-space:nowrap}
.call strong{font-weight:800}
.site{left:562px;top:1507px;width:462px;height:34px;border:2px solid #fff;color:#fff;font-size:19px;font-weight:500;display:flex;align-items:center;justify-content:center}
</style>
</head>
<body>
<main class="flyer">
  <div class="abs hero-band"></div>
  <svg class="abs hero-photo" width="1100" height="478" viewBox="0 0 1100 478" role="img" aria-label="Photo of hands working with a calculator, pen and financial charts on a desk">
    <defs>
      <linearGradient id="deskTone" x1="0" y1="0" x2="1" y2="1">
        <stop offset="0" stop-color="#f1ead9"/>
        <stop offset=".55" stop-color="#c9cfd6"/>
        <stop offset="1" stop-color="#6f8aa3"/>
      </linearGradient>
    </defs>
    <polygon points="565,196 616,0 1100,0 1100,478 681,478" fill="var(--teal-light)"/>
    <polygon points="590,196 636,0 1100,0 1100,478 700,478" fill="url(#deskTone)"/>
  </svg>

  <div class="abs brand">
    <div class="brand-mark"></div>
    <div>
      <div class="brand-name">EVEN LEDGER</div>
      <div class="brand-sub">Financial Services</div>
    </div>
  </div>

  <h1 class="abs headline">BOOKKEEPING<br>TAILORED</h1>
  <div class="abs tagline">TO YOUR BUSINESS NEEDS</div>

  <svg class="abs intro-icon" width="104" height="110" viewBox="0 0 104 110" aria-hidden="true">
    <g fill="none" stroke="var(--teal-deep)" stroke-width="3">
      <rect x="38" y="6" width="54" height="74" rx="3"/>
      <rect x="30" y="14" width="54" height="74" rx="3" fill="#fff"/>
      <line x1="50" y1="30" x2="74" y2="30"/><line x1="50" y1="40" x2="74" y2="40"/><line x1="50" y1="50" x2="74" y2="50"/><line x1="50" y1="60" x2="74" y2="60"/>
      <path d="M8 42 L30 34 L52 42 V62 C52 78 30 90 30 90 C30 90 8 78 8 62 Z" fill="#fff" stroke="var(--teal)"/>
      <path d="M20 62 L28 70 L42 54" stroke="var(--teal)"/>
    </g>
  </svg>
  <div class="abs intro">
    Are you a small business owner,<br>
    <span class="accent">Tradie or TRPQ Service Provider</span> struggling to stay on top of your<br>
    <span class="intro-head">BOOKKEEPING &amp; COMPLIANCE OBLIGATIONS?</span>
  </div>
  <p class="abs intro-box">If so we would love to help you get back on track and take control of your business finances so that you can make informed business decisions and focus on what you do best.</p>

  <div class="abs side-photo" role="img" aria-label="Photo of a hand writing in a notebook beside printed financial charts" style="background:linear-gradient(160deg,#eef1f5 0%,#c9d6e4 55%,#5f86b4 100%)"></div>
  <svg class="abs seal" width="176" height="176" viewBox="0 0 176 176" role="img" aria-label="Registration badge placeholder">
    <circle cx="88" cy="88" r="84" fill="var(--gray-soft)" stroke="var(--gray-dark)" stroke-width="3"/>
  </svg>
  <p class="abs bas">BAS AGENT 81234567</p>

  <div class="abs years"><div class="small">We have over</div><div class="big">20 YEARS</div></div>
  <div class="abs years-divider"></div>
  <p class="abs years-note">industry experience and,<br>as a small business ourselves</p>

  <svg class="abs offer" width="709" height="196" viewBox="0 0 709 196" aria-hidden="true">
    <rect width="709" height="196" fill="var(--teal)"/>
    <polygon points="0,0 484,0 583,196 0,196" fill="var(--gray)"/>
  </svg>
  <div class="abs offer-text">
    <div class="small">We are able to offer our clients a</div>
    <div class="big">PERSONAL BOOKKEEPING</div>
    <div class="big teal">SOLUTION TAILORED</div>
    <div class="small">to meet the needs of your business.</div>
  </div>

  <ul class="abs services col-a">
    <li style="margin-bottom:14px"><svg width="20" height="20" viewBox="0 0 20 20"><circle cx="10" cy="10" r="10" fill="var(--teal)"/><path d="M5 10 L9 14 L15 7" stroke="#fff" stroke-width="2.5" fill="none"/></svg>Accounts Payable</li>
    <li style="margin-bottom:12px"><svg width="20" height="20" viewBox="0 0 20 20"><circle cx="10" cy="10" r="10" fill="var(--teal)"/><path d="M5 10 L9 14 L15 7" stroke="#fff" stroke-width="2.5" fill="none"/></svg>Customer Invoicing</li>
    <li style="margin-bottom:27px"><svg width="20" height="20" viewBox="0 0 20 20"><circle cx="10" cy="10" r="10" fill="var(--teal)"/><path d="M5 10 L9 14 L15 7" stroke="#fff" stroke-width="2.5" fill="none"/></svg>Business Activity</li>
    <li style="margin-bottom:28px"><svg width="20" height="20" viewBox="0 0 20 20"><circle cx="10" cy="10" r="10" fill="var(--teal)"/><path d="M5 10 L9 14 L15 7" stroke="#fff" stroke-width="2.5" fill="none"/></svg>Superannuation</li>
    <li style="margin-bottom:12px"><svg width="20" height="20" viewBox="0 0 20 20"><circle cx="10" cy="10" r="10" fill="var(--teal)"/><path d="M5 10 L9 14 L15 7" stroke="#fff" stroke-width="2.5" fill="none"/></svg>Payroll</li>
    <li><svg width="20" height="20" viewBox="0 0 20 20"><circle cx="10" cy="10" r="10" fill="var(--teal)"/><path d="M5 10 L9 14 L15 7" stroke="#fff" stroke-width="2.5" fill="none"/></svg>Vantly &amp; Brimfolk<br>Set-Up and Training</li>
  </ul>
  <div class="abs col-divider"></div>
  <ul class="abs services col-b">
    <li style="margin-bottom:14px"><svg width="20" height="20" viewBox="0 0 20 20"><circle cx="10" cy="10" r="10" fill="var(--teal)"/><path d="M5 10 L9 14 L15 7" stroke="#fff" stroke-width="2.5" fill="none"/></svg>Accounts Receivable</li>
    <li style="margin-bottom:14px"><svg width="20" height="20" viewBox="0 0 20 20"><circle cx="10" cy="10" r="10" fill="var(--teal)"/><path d="M5 10 L9 14 L15 7" stroke="#fff" stroke-width="2.5" fill="none"/></svg>Bank &amp; Credit Card<br>Reconciliations</li>
    <li style="margin-bottom:14px"><svg width="20" height="20" viewBox="0 0 20 20"><circle cx="10" cy="10" r="10" fill="var(--teal)"/><path d="M5 10 L9 14 L15 7" stroke="#fff" stroke-width="2.5" fill="none"/></svg>Regular Financial<br>Reports</li>
    <li style="margin-bottom:14px"><svg width="20" height="20" viewBox="0 0 20 20"><circle cx="10" cy="10" r="10" fill="var(--teal)"/><path d="M5 10 L9 14 L15 7" stroke="#fff" stroke-width="2.5" fill="none"/></svg>Payroll Tax</li>
    <li><svg width="20" height="20" viewBox="0 0 20 20"><circle cx="10" cy="10" r="10" fill="var(--teal)"/><path d="M5 10 L9 14 L15 7" stroke="#fff" stroke-width="2.5" fill="none"/></svg>Instalment Activity<br>Statements</li>
  </ul>

  <svg class="abs footer" width="1100" height="126" viewBox="0 0 1100 126" aria-hidden="true">
    <defs>
      <linearGradient id="footTeal" x1="0" x2="1">
        <stop offset="0" stop-color="var(--teal)"/>
        <stop offset="1" stop-color="var(--teal-deep)"/>
      </linearGradient>
    </defs>
    <rect width="1100" height="126" fill="var(--gray)"/>
    <polygon points="426,0 1100,0 1100,126 513,126" fill="url(#footTeal)"/>
  </svg>
  <div class="abs partners">
    <div class="partner" style="background:#19b5e6"></div>
    <div class="partner" style="background:#1f7f99"></div>
    <div class="partner" style="background:#f4f5f2;border-radius:8px"></div>
    <div class="partner" style="background:#2c3b2e"></div>
  </div>
  <div class="abs call">CALL US
    <svg width="34" height="34" viewBox="0 0 24 24" aria-hidden="true"><path fill="#fff" d="M6.6 10.8c1.4 2.8 3.8 5.1 6.6 6.6l2.2-2.2c.3-.3.7-.4 1-.2 1.1.4 2.3.6 3.6.6.6 0 1 .4 1 1V20c0 .6-.4 1-1 1C10.6 21 3 13.4 3 4c0-.6.4-1 1-1h3.5c.6 0 1 .4 1 1 0 1.3.2 2.5.6 3.6.1.3 0 .7-.2 1z"/></svg>
    <strong>0491 570 156</strong></div>
  <div class="abs site">www.evenledgerfinancial.com.au</div>
</main>
</body>
</html>
```